Harbourline Electrical Solutions

On one side. LOGO (underneath:) Commercial Industrial Residential

- NAME & CONTACT DETAILS

Marcus T. Hollings
Project Manager

(Cell icon) (441) 555-0187
(Email icon) hlelectricalsolutions@mailvento.com
(Facebook & Instagram icons )@hlelectricalsolutions

Other side: LOGO - underneath ELECTRICAL CONSTRUCTION & MAINTENANCE . LED LIGHTING & AUTOMATION . LIFE SAFETY SYSTEMS (FIRE ALARM / SECURITY) . DATA & COMMUNICATION

```html
<!DOCTYPE html>
<html lang="en">
<head>
<meta charset="utf-8">
<title>Harbourline Electrical Solutions – Business Card</title>
<link href="https://fonts.googleapis.com/css2?family=Montserrat:wght@400;500;600&family=Roboto:wght@400&family=Saira+Semi+Condensed:ital,wght@1,500&display=swap" rel="stylesheet">
<style>
  :root {
    --bg: #5a5a5a;
    --bg-dark: #3c3c3c;
    --card: #1e1f21;
    --ink: #e6e6e6;
    --muted: #a9a9a9;
    --silver: #8c8c8c;
    --blue: #1b8fd6;
    --teal: #1f6e92;
  }
  * { margin: 0; padding: 0; box-sizing: border-box; }
  html, body { width: 799px; height: 1200px; overflow: hidden; }
  body {
    background: radial-gradient(ellipse at 60% 40%, var(--bg), var(--bg-dark));
    font-family: "Montserrat", sans-serif;
    color: var(--ink);
    position: relative;
  }
  .card {
    position: absolute;
    left: 60px;
    width: 680px;
    height: 389px;
    background: var(--card);
    border-radius: 4px;
    box-shadow: 0 14px 30px rgba(0,0,0,.45);
  }
  .card--front { top: 140px; }
  .card--back { top: 670px; }

  /* front */
  .wordmark {
    position: absolute;
    font-weight: 500;
    text-transform: uppercase;
    line-height: 1.12;
    letter-spacing: 4px;
  }
  .card--front .wordmark {
    left: 150px; top: 60px;
    font-size: 30px;
    color: var(--silver);
  }
  .services {
    position: absolute;
    left: 60px; top: 210px;
    font-family: "Roboto", sans-serif;
    font-size: 15.5px;
    line-height: 1.5;
    color: var(--ink);
  }
  .rule {
    position: absolute;
    height: 2px;
    background: var(--blue);
  }
  .card--front .rule { left: 40px; right: 40px; top: 270px; }
  .sectors {
    position: absolute;
    font-weight: 500;
    letter-spacing: 2.5px;
    text-transform: uppercase;
    white-space: nowrap;
  }
  .card--front .sectors { left: 60px; top: 300px; font-size: 15px; color: var(--ink); }
  .sectors .sep { margin: 0 16px; }

  /* back */
  .card--back .wordmark {
    right: 40px; top: 50px;
    font-size: 28px;
    text-align: right;
    color: var(--teal);
  }
  .card--back .sectors {
    right: 40px; top: 160px;
    font-size: 12.5px;
    color: var(--ink);
  }
  .contact { position: absolute; left: 40px; top: 205px; }
  .contact__name {
    font-family: "Saira Semi Condensed", sans-serif;
    font-style: italic;
    font-weight: 500;
    font-size: 26px;
    color: var(--teal);
  }
  .contact__role {
    font-family: "Roboto", sans-serif;
    font-size: 15px;
    color: var(--ink);
    margin-bottom: 6px;
  }
  .contact__line {
    display: flex; align-items: center; gap: 10px;
    font-family: "Roboto", sans-serif;
    font-size: 15px;
    color: var(--ink);
    line-height: 1.55;
  }
  .contact__line svg { width: 14px; height: 14px; fill: var(--teal); flex: none; }
  .card--back .rule { left: 200px; right: 40px; top: 262px; height: 1.5px; background: var(--teal); }
  .social { position: absolute; right: 40px; top: 315px; }
  .social__line {
    display: flex; align-items: center; justify-content: flex-end; gap: 10px;
    font-family: "Roboto", sans-serif;
    font-size: 15px;
    line-height: 1.65;
  }
  .social__mark {
    width: 14px; height: 14px;
    border: 1.5px solid var(--teal);
    border-radius: 3px;
  }
</style>
</head>
<body>

<section class="card card--front" aria-label="Card front">
  <div class="wordmark">Harbourline<br>Electrical<br>Solutions</div>
  <p class="services">
    Electrical Construction &amp; Maintenance | Led Lighting &amp; Automation<br>
    Life Safety Systems (Fire Alarm/Security) | Data &amp; Communication
  </p>
  <div class="rule"></div>
  <p class="sectors">Commercial<span class="sep">|</span>Industrial<span class="sep">|</span>Residential</p>
</section>

<section class="card card--back" aria-label="Card back">
  <div class="wordmark">Harbourline<br>Electrical<br>Solutions</div>
  <p class="sectors">Commercial<span class="sep">|</span>Industrial<span class="sep">|</span>Residential</p>

  <div class="contact">
    <p class="contact__name">Marcus T. Hollings</p>
    <p class="contact__role">Project Manager</p>
    <p class="contact__line">
      <svg viewBox="0 0 24 24" aria-hidden="true"><path d="M6.6 10.8a15.2 15.2 0 0 0 6.6 6.6l2.2-2.2a1 1 0 0 1 1-.25 11.4 11.4 0 0 0 3.6.57 1 1 0 0 1 1 1V20a1 1 0 0 1-1 1A17 17 0 0 1 3 4a1 1 0 0 1 1-1h3.5a1 1 0 0 1 1 1c0 1.25.2 2.45.57 3.57a1 1 0 0 1-.25 1z"/></svg>
      (441) 555-0187
    </p>
    <p class="contact__line">
      <svg viewBox="0 0 24 24" aria-hidden="true"><path d="M2 5h20v14H2z M4 7v.4l8 5.1 8-5.1V7l-8 5z" fill-rule="evenodd"/></svg>
      hlelectricalsolutions@mailvento.com
    </p>
  </div>
  <div class="rule"></div>

  <div class="social">
    <p class="social__line">@hlelectricalsolutions <span class="social__mark"></span></p>
    <p class="social__line">@hlelectricalsolutions <span class="social__mark"></span></p>
  </div>
</section>

</body>
</html>
```